Northvale Strategy Partners Website Design

I need a website design for my new business consulting and executive coaching firm, Northvale Strategy Partners. We provide consultative services to business C-suites as well as personal coaching to executives. I have attached the logo with color scheme I have chosen. I would like the website to reflect professionalism and continue the color scheme in the logo.

Target Market(s)

Small to medium business and their executives; middle to upper income men and women in mid- to late career looking for significance

Industry/Entity Type

Business Consultant

Number of Pages Required

4 page

Requirements
Must have
• A homepage with prominent logo and way to contact for more information; an area on the homepage with easy to read, clear text to describe what the company does; a prominent area on the homepage for a tagline; a blog page that can be updated regularly, an "about us" page with biographical information; an "about us" page; a page detailing services offered
• The web design must match the logo colors and font that I have uploaded.
Nice to have
• A lighthouse picture in the background or header
Should not have
• A lot of text area on the homepage

```html
<!DOCTYPE html>
<html lang="en">
<head>
<meta charset="utf-8">
<title>Northvale Strategy Partners</title>
<link rel="stylesheet" href="https://fonts.googleapis.com/css2?family=Archivo+Black&family=Open+Sans:wght@400;600;700&family=Marcellus&display=swap">
<style>
:root{
  --navy:#1c2a5a;
  --maroon:#6e0b0e;
  --maroon-dark:#5c0a0c;
  --light:#e8e8e8;
  --text:#444;
  --white:#fff;
  --black:#0b0b0b;
}
*{box-sizing:border-box;margin:0;padding:0}
html,body{width:1200px;height:2752px;overflow:hidden}
body{position:relative;font-family:"Open Sans",Arial,sans-serif;color:var(--text);background:var(--white)}
.abs{position:absolute}
.heading{font-family:"Archivo Black",Arial,sans-serif;color:var(--navy);letter-spacing:.5px}
.heading span{color:var(--maroon)}

/* header */
.site-header{top:0;left:0;width:1200px;height:130px;background:var(--white)}
.brand{left:79px;top:40px;display:flex;align-items:center;gap:12px}
.brand-mark{width:26px;height:26px;background:var(--navy)}
.brand-name{font-family:"Marcellus",serif;font-size:22px;color:var(--navy);line-height:1.1;width:170px}
.nav a{position:absolute;top:0;height:130px;line-height:136px;font-size:15px;color:#111;text-decoration:none}
.nav .active{left:481px;width:104px;background:var(--maroon);color:var(--white);text-align:center}

/* hero */
.hero{top:130px;left:0;width:1200px;height:521px;background:linear-gradient(180deg,#2b3a55 0%,#4a5870 45%,#8a7356 75%,#3b3530 100%)}
.hero-rule{left:303px;width:594px;height:2px;background:rgba(255,255,255,.8)}
.hero-title{left:303px;width:594px;top:298px;text-align:center;font-family:"Archivo Black",Arial,sans-serif;font-size:31px;color:var(--white)}
.hero-sub{left:290px;width:620px;top:356px;text-align:center;font-size:16px;line-height:22px;color:var(--navy);font-weight:600}
.circle-btn{width:62px;height:62px;border-radius:50%;border:2px solid var(--white);color:var(--white);display:flex;align-items:center;justify-content:center;font-size:30px;font-weight:700}
.circle-btn.filled{background:var(--maroon)}

/* about */
.about-divider{left:391px;top:697px;width:1px;height:288px;background:#ccc}
.about-rule{left:391px;top:793px;width:681px;height:1px;background:#ccc}
.about-logo{left:110px;top:800px;display:flex;align-items:center;gap:14px}
.about-logo .brand-mark{width:34px;height:34px}
.about-logo .brand-name{font-size:26px;width:220px}
.about-title{left:435px;top:724px;font-size:33px}
.about-text{left:435px;top:824px;width:625px;font-size:17.5px;line-height:29px;color:#555}

/* services */
.services{top:1037px;left:0;width:1200px;height:438px;background:linear-gradient(90deg,#2a2a2a,#3a3a3a 50%,#2d2d2d)}
.services-title{left:0;width:1200px;top:1094px;text-align:center;font-family:"Archivo Black",Arial,sans-serif;font-size:30px;color:var(--white)}
.services-divider{left:599px;top:1165px;height:252px;border-left:2px dashed rgba(255,255,255,.7)}
.service-icon{width:110px;height:110px;border-radius:50%;background:rgba(255,255,255,.85)}
.service-name{width:480px;text-align:center;font-family:"Marcellus",serif;font-size:25px;color:var(--white)}
.service-text{width:400px;text-align:center;font-size:14.5px;line-height:24px;color:var(--white)}

/* subscribe */
.subscribe{top:1475px;left:0;width:1200px;height:156px;background:var(--light)}
.subscribe-input{left:125px;top:1529px;width:638px;height:55px;border:2px solid #ccc;background:#eee;font-family:"Marcellus",serif;font-size:18px;color:#666;line-height:51px;padding-left:20px}
.subscribe-btn{left:771px;top:1529px;width:207px;height:55px;background:var(--maroon);color:var(--white);font-weight:700;font-size:17px;display:flex;align-items:center;justify-content:center;gap:14px}

/* testimonials */
.testi-title{left:0;width:1200px;top:1678px;text-align:center;font-size:33px}
.testimonial{width:310px}
.quote-mark{font-family:Georgia,serif;font-size:110px;line-height:80px;color:#d8d8d8;height:40px;overflow:visible}
.testimonial p{font-size:15px;line-height:23px;color:#444;margin-top:-6px}
.testimonial .name{font-family:"Marcellus",serif;font-size:19px;color:var(--maroon);margin-top:14px;font-weight:700}
.testimonial .role{font-size:14px;color:var(--maroon);margin-top:2px}
.circle-btn.dark{border-color:#555;color:#222;background:var(--white)}

/* blog */
.blog{top:2042px;left:0;width:1200px;height:334px;background:var(--light)}
.blog-title{left:0;width:1200px;top:2095px;text-align:center;font-size:33px}
.blog-text{left:210px;width:780px;top:2174px;text-align:center;font-size:15px;line-height:28px;color:#444}
.blog-text b{color:#222}
.read-more{left:0;width:1200px;top:2234px;text-align:center;font-weight:700;font-size:17px;color:var(--maroon);text-decoration:underline}
.blog-meta{top:2291px;display:flex;align-items:center;gap:10px;font-size:13px;color:#555}

/* footer */
.footer{top:2376px;left:0;width:1200px;height:314px;background:var(--maroon)}
.footer-heading{font-family:"Marcellus",serif;font-size:18px;color:var(--white);font-weight:700}
.contact-row{left:79px;display:flex;gap:20px;color:var(--white);font-size:15px;line-height:24px}
.contact-row svg{flex:none;margin-top:2px}
.footer-brand{left:480px;width:240px;top:2455px;text-align:center;font-family:"Marcellus",serif;font-size:24px;line-height:30px;color:var(--white)}
.social{width:36px;height:36px;border-radius:50%;background:var(--maroon-dark);border:1px solid rgba(255,255,255,.3)}
.social.first{background:var(--white)}
.footer-nav a{position:absolute;left:912px;width:211px;height:40px;border-bottom:1px solid rgba(255,255,255,.85);color:var(--white);text-decoration:none;font-family:"Marcellus",serif;font-size:17px;padding-left:32px;line-height:34px}
.footer-nav a::before{content:"";position:absolute;left:6px;top:12px;border-left:8px solid #ff2b2b;border-top:6px solid transparent;border-bottom:6px solid transparent}
.bottom-bar{top:2690px;left:0;width:1200px;height:62px;background:var(--black);color:#ddd;font-size:12px;text-align:center;line-height:62px}
.bottom-bar span{color:#c21a1a}
</style>
</head>
<body>

<header class="abs site-header">
  <div class="abs brand"><div class="brand-mark"></div><div class="brand-name">Northvale Strategy Partners</div></div>
  <nav class="nav">
    <a class="active" href="#">HOME</a>
    <a style="left:596px" href="#">ABOUT US</a>
    <a style="left:712px" href="#">SERVICES</a>
    <a style="left:818px" href="#">TESTIMONIAL</a>
    <a style="left:952px" href="#">BLOG</a>
    <a style="left:1033px" href="#">CONTACT US</a>
  </nav>
</header>

<section class="abs hero" role="img" aria-label="Lighthouse beneath a stormy evening sky"></section>
<div class="abs hero-rule" style="top:294px"></div>
<h1 class="abs hero-title">LOREM IPSUME DOLOR SIT AMET</h1>
<div class="abs hero-rule" style="top:345px"></div>
<p class="abs hero-sub">Lorem ipsum dolor sit amet, consectetur adipiscing elit, sed do eiusmod tempor incididunt ut labore et dolore magna aliqua.</p>
<div class="abs circle-btn filled" style="left:532px;top:419px">«</div>
<div class="abs circle-btn" style="left:606px;top:419px">»</div>

<div class="abs about-logo"><div class="brand-mark"></div><div class="brand-name">Northvale Strategy Partners</div></div>
<div class="abs about-divider"></div>
<h2 class="abs heading about-title">KNOW <span>ABOUT US</span></h2>
<div class="abs about-rule"></div>
<p class="abs about-text">Lorem ipsum dolor sit amet, consectetur adipiscing elit, sed do eiusmod tempor incididunt ut labore et dolore magna aliqua. Ut enim ad minim veniam, quis nostrud exercitation ullamco laboris nisi ut aliquip ex ea commodo consequat. Duis aute irure dolor in reprehenderit.</p>

<section class="abs services" role="img" aria-label="Business professionals talking in an office, darkened"></section>
<h2 class="abs services-title">WHAT WE DO</h2>
<div class="abs services-divider"></div>
<div class="abs service-icon" role="img" aria-label="Consultation icon" style="left:270px;top:1178px"></div>
<h3 class="abs service-name" style="left:85px;top:1310px">Consultative Services</h3>
<p class="abs service-text" style="left:125px;top:1355px">Lorem ipsum dolor sit amet, consectetur adipiscing elit, sed do eiusmod tempor incididunt.</p>
<div class="abs service-icon" role="img" aria-label="Coaching icon" style="left:826px;top:1178px"></div>
<h3 class="abs service-name" style="left:641px;top:1310px">Executive Coaching</h3>
<p class="abs service-text" style="left:681px;top:1355px">Lorem ipsum dolor sit amet, consectetur adipiscing elit, sed do eiusmod tempor incididunt.</p>

<section class="abs subscribe"></section>
<div class="abs subscribe-input">SUBSCRIBE HERE | EMAIL ID</div>
<div class="abs subscribe-btn">SEND
  <svg width="20" height="20" viewBox="0 0 20 20"><path d="M19 1 1 9l6 2 2 7 3-5 5 3z" fill="#fff"/></svg>
</div>

<h2 class="abs heading testi-title">WHAT OUR <span>CLIENT SAY</span></h2>
<div class="abs testimonial" style="left:79px;top:1752px">
  <div class="quote-mark">“</div>
  <p>Lorem ipsum dolor sit amet, consectetur adipiscing elit, sed do eiusmod tempor incididunt ut labore et dolore magna aliqua.</p>
  <div class="name">-Name Here</div><div class="role">Designation here</div>
</div>
<div class="abs testimonial" style="left:459px;top:1752px">
  <div class="quote-mark">“</div>
  <p>Lorem ipsum dolor sit amet, consectetur adipiscing elit, sed do eiusmod tempor incididunt ut labore et dolore magna aliqua.</p>
  <div class="name">-Name Here</div><div class="role">Designation here</div>
</div>
<div class="abs testimonial" style="left:833px;top:1752px">
  <div class="quote-mark">“</div>
  <p>Lorem ipsum dolor sit amet, consectetur adipiscing elit, sed do eiusmod tempor incididunt ut labore et dolore magna aliqua.</p>
  <div class="name">-Name Here</div><div class="role">Designation here</div>
</div>
<div class="abs circle-btn dark" style="left:541px;top:1943px;width:54px;height:54px;font-size:26px">«</div>
<div class="abs circle-btn dark" style="left:604px;top:1943px;width:54px;height:54px;font-size:26px">»</div>

<section class="abs blog"></section>
<h2 class="abs heading blog-title">OUR LATEST <span>BLOG</span></h2>
<p class="abs blog-text"><b>Lorem ipsum dolor sit amet</b>, consectetur adipiscing elit, sed do eiusmod tempor incididunt ut labore et dolore magna aliqua. Ut enim ad minim veniam, quis nostrud exercitation ullamco labori</p>
<div class="abs read-more">READ MORE</div>
<div class="abs blog-meta" style="left:416px">
  <svg width="20" height="20" viewBox="0 0 20 20"><rect x="2" y="4" width="16" height="14" fill="none" stroke="#6e0b0e" stroke-width="2"/><path d="M2 8h16M6 2v4M14 2v4" stroke="#6e0b0e" stroke-width="2"/></svg>29-12-2015</div>
<div class="abs blog-meta" style="left:547px">
  <svg width="22" height="20" viewBox="0 0 22 20"><path d="M11 3c5 0 9 3 9 6.5S16 16 11 16c-1 0-2 0-3-.3L3 18l2-4C3 12.8 2 11.2 2 9.5 2 6 6 3 11 3z" fill="none" stroke="#333" stroke-width="1.8"/></svg>20-Comment</div>
<div class="abs blog-meta" style="left:693px">
  <svg width="22" height="16" viewBox="0 0 22 16"><path d="M1 8s4-6 10-6 10 6 10 6-4 6-10 6S1 8 1 8z" fill="none" stroke="#6e0b0e" stroke-width="2"/><circle cx="11" cy="8" r="3" fill="#6e0b0e"/></svg>20 - View</div>

<footer class="abs footer"></footer>
<div class="abs footer-heading" style="left:79px;top:2424px">KEEP IN TOUCH</div>
<div class="abs contact-row" style="top:2490px">
  <svg width="20" height="18" viewBox="0 0 20 18"><path d="M10 1 1 9h3v8h5v-5h2v5h5V9h3z" fill="#fff"/></svg>
  <span>Lorem ipsum dolor sit amet,<br>consectetur adipiscing elit, sed do.</span></div>
<div class="abs contact-row" style="top:2557px">
  <svg width="20" height="20" viewBox="0 0 20 20"><path d="M4 1l4 4-2 3c1 2 4 5 6 6l3-2 4 4-3 3C9 19 1 11 1 4z" fill="#fff"/></svg>
  <span>+10 555 014 2290</span></div>
<div class="abs contact-row" style="top:2601px">
  <svg width="20" height="16" viewBox="0 0 20 16"><rect x="1" y="2" width="18" height="13" fill="#fff"/><path d="M1 2l9 7 9-7" fill="none" stroke="#6e0b0e" stroke-width="1.5"/></svg>
  <span>hello@northvalesp.com</span></div>

<div class="abs footer-brand">Northvale Strategy Partners</div>
<div class="abs social first" style="left:520px;top:2569px"></div>
<div class="abs social" style="left:562px;top:2569px"></div>
<div class="abs social" style="left:602px;top:2569px"></div>
<div class="abs social" style="left:644px;top:2569px"></div>

<div class="abs footer-heading" style="left:912px;top:2424px">NAVIGATION</div>
<nav class="footer-nav">
  <a class="abs" style="top:2455px" href="#">Home</a>
  <a class="abs" style="top:2495px" href="#">About Us</a>
  <a class="abs" style="top:2535px" href="#">Services</a>
  <a class="abs" style="top:2575px" href="#">Blog</a>
  <a class="abs" style="top:2615px;border-bottom:none" href="#">Contact Us</a>
</nav>

<div class="abs bottom-bar">© <span>NORTHVALE STRATEGY PARTNERS</span> - 2015. All Rights Reserved</div>

</body>
</html>
```